Garlic Farm for Farm Sales/Restaurant sales

Need a professional, but appealing to agriculture world. We are selling 27 kinds of Organic Garlic from a farm in Simla,CO. I have uploaded logo and business information-we are going to need a template, because I will need to use it for four separate people.
-We are trying to appeal to Farm to table restaurants
-As well as growers/farmers

Target Market(s)

Agriculture Sales/Restaurants-Organic

Industry/Entity Type

Agriculture

Contact Information for Business Card

Want it to look more unique then your average kelto stock card- I want it to look amazing

Font styles to use
Sans Serif

Colors
0455a3
ec1f27
fbed22
ffffff

Requirements
Must have
• Just be creative
Nice to have
• Colorful
Should not have
• plain

```html
<!DOCTYPE html>
<html lang="en">
<head>
<meta charset="utf-8">
<title>Summit Clove – Business Card</title>
<link rel="stylesheet" href="https://fonts.googleapis.com/css2?family=PT+Sans:wght@400;700&display=swap">
<style>
  :root {
    --coral: #cf4b43;
    --crimson: #a3173a;
    --sun: #fbd80a;
    --navy: #062c5e;
    --ink: #0c2d6b;
    --backdrop: #ece8e4;
  }
  * { margin: 0; padding: 0; box-sizing: border-box; }
  html, body {
    width: 1200px; height: 900px; overflow: hidden;
    background: var(--backdrop);
    font-family: "PT Sans", sans-serif;
  }
  .stage { position: relative; width: 1200px; height: 900px; }

  .card { position: absolute; }
  .card svg { position: absolute; inset: 0; overflow: visible; }

  .card-front { left: 135px; top: 67px; width: 585px; height: 363px; }
  .card-back  { left: 445px; top: 462px; width: 565px; height: 350px; }

  .holder { position: absolute; left: 20px; top: 36px; color: var(--sun); }
  .holder-name { font-size: 21px; font-weight: 700; line-height: 1.15; }
  .holder-role { font-size: 15px; line-height: 1.3; }

  .address {
    position: absolute; left: 17px; top: 163px;
    font-size: 15.5px; line-height: 1.15; color: var(--ink);
  }

  .contact-list {
    position: absolute; left: 20px; top: 270px;
    list-style: none; color: var(--sun); font-size: 15px;
  }
  .contact-list li { display: flex; align-items: center; gap: 10px; height: 24.5px; }
  .contact-list svg { position: static; width: 12px; height: 12px; fill: var(--sun); }

  .brand {
    position: absolute; display: flex; align-items: center; gap: 10px;
    font-weight: 700; white-space: nowrap;
  }
  .brand-dot { border-radius: 50%; flex: none; }

  .card-front .brand {
    left: 300px; top: 160px; width: 240px; justify-content: center;
    color: var(--ink); font-size: 32px;
  }
  .card-front .brand-dot { width: 22px; height: 22px; background: var(--crimson); }

  .card-back .brand {
    left: 30px; top: 152px; width: 280px; justify-content: center;
    color: var(--sun); font-size: 34px;
  }
  .card-back .brand-dot { width: 22px; height: 22px; background: var(--sun); }
</style>
</head>
<body>
<main class="stage">

  <section class="card card-front" aria-label="Business card, front">
    <svg width="585" height="363" viewBox="0 0 585 363" aria-hidden="true">
      <path class="card-shape" fill="var(--coral)"
            d="M0 0 H420 A165 165 0 0 1 585 178 A165 185 0 0 1 420 363 H0 Z"/>
      <rect class="info-band" x="0" y="103" width="430" height="155" fill="var(--sun)"/>
      <circle class="emblem-ring" cx="420" cy="178" r="160" fill="var(--crimson)"/>
      <circle class="emblem-disc" cx="420" cy="178" r="150" fill="var(--sun)"/>
      <path class="emblem-stroke" d="M262 250 A160 160 0 0 0 470 335" fill="none"
            stroke="var(--navy)" stroke-width="7" stroke-linecap="round"/>
    </svg>

    <div class="holder">
      <p class="holder-name">Marcus Hale</p>
      <p class="holder-role">Managing Director</p>
    </div>

    <p class="address">12345, Address Goes Here<br>Country Name, 123456</p>

    <ul class="contact-list">
      <li><svg viewBox="0 0 12 12"><path d="M2 0 L4.5 0 L5.5 3 L4 4.5 Q5.5 7.5 7.5 8 L9 6.5 L12 7.5 L12 10 Q11 12 9 12 Q1 10 0 2 Q0 0 2 0Z"/></svg>(044)-555-0182</li>
      <li><svg viewBox="0 0 12 12"><path d="M0 2 H12 V10 H0 Z M0 2 L6 7 L12 2" fill="var(--sun)" stroke="var(--coral)" stroke-width="1"/></svg>hello@summitclove.com</li>
      <li><svg viewBox="0 0 12 12"><circle cx="6" cy="6" r="6"/><path d="M1 6 H11 M6 0.5 Q2.5 6 6 11.5 M6 0.5 Q9.5 6 6 11.5" stroke="var(--coral)" stroke-width="1" fill="none"/></svg>www.summitclove.com</li>
    </ul>

    <div class="brand"><span class="brand-dot"></span>Summit Clove</div>
  </section>

  <section class="card card-back" aria-label="Business card, back">
    <svg width="565" height="350" viewBox="0 0 565 350" aria-hidden="true">
      <rect class="card-shape" x="170" y="0" width="395" height="350" fill="var(--coral)"/>
      <circle class="card-shape" cx="172" cy="175" r="172" fill="var(--coral)"/>
      <circle class="emblem-ring" cx="172" cy="175" r="160" fill="var(--crimson)"/>
      <circle class="emblem-disc" cx="172" cy="175" r="150" fill="var(--navy)"/>
      <rect class="brand-band" x="250" y="100" width="315" height="150" fill="var(--navy)"/>
    </svg>

    <div class="brand"><span class="brand-dot"></span>Summit Clove</div>
  </section>

</main>
</body>
</html>
```